Ledger Lanternfox Powerpoint with Marshal Valorline Type Theme

Need powerpoint template with matching colors and different slide options. Logo and colors to be used can be found at ledgerlanternfox.example. Want brightly colored slide deck that is readable form the back of a room, but highlights colors. I will be incorporating Quizzap into the slides to gamify my presentations.

Target Market(s)

Tech

Industry/Entity Type

IT, specifically database, but crossing over to mental health in IT, important note this is not for a company, this is just for a professional building a brand

Font styles to use
Sans Serif

Colors
0054AA
0677BA
7BADD7
CADEEF
E8F1F8
EB3D1F
EC4F4E
F09395
F8D3D4
FCEDEE

Requirements
Must have
• My Logo in the bottom corner, front page, a thank your page, question page, content page, content page with two columns, content page with graphs, and icons to be used in the primary colors of the logos, About Me Page, Break Slides, Demo break slide
Should not have
• Lighter shades of colors, I want to pop out where colors are used, I want spacing and font size to be readable from the back of a room, most likely black text and white background

```html
<!DOCTYPE html>
<html lang="en">
<head>
<meta charset="utf-8">
<title>Ledger Lanternfox – Slide Deck Theme</title>
<link rel="stylesheet" href="https://fonts.googleapis.com/css2?family=Raleway:wght@300;400;500;600;700;800&display=swap">
<style>
:root{
  --navy:#1b3f7c;
  --navy-deep:#133262;
  --navy-ink:#0f2a52;
  --red:#e8262c;
  --red-soft:#f4c9ca;
  --charcoal:#3d3d3f;
  --gray:#8b8b8d;
  --ink:#3a3a3a;
  --muted:#8d94a3;
  --line:#dde2ea;
  --board:#eceef2;
  --white:#ffffff;
}
*{box-sizing:border-box;margin:0;padding:0}
html,body{width:1200px;height:3404px;overflow:hidden;background:var(--board)}
body{font-family:"Raleway",Arial,sans-serif;color:var(--ink)}
.board{display:grid;grid-template-columns:repeat(3,387px);grid-auto-rows:217px;gap:9px;padding:11px 10px}
.slide{position:relative;overflow:hidden;background:var(--white)}
.slide > *{position:absolute}
.fill-navy{background:var(--navy)}
.fill-charcoal{background:var(--charcoal)}
.fill-red{background:var(--red)}
.photo{inset:0}
.photo-city{background:linear-gradient(135deg,#2a4f8c 0%,#1b3f7c 55%,#142f60 100%)}
.photo-dark{background:linear-gradient(120deg,#1d3b70,#2c5592 60%,#1a376c)}
.photo-desk{background:linear-gradient(150deg,#f3f4f6 0%,#d9dde3 45%,#9aa3b1 100%)}
.photo-mountain{background:linear-gradient(180deg,#5d6b78 0%,#323a44 60%,#1d2229 100%)}
.photo-keyboard{background:linear-gradient(135deg,#5b4a7a,#2c2c3a 60%,#8a8fa0)}
.portrait{border-radius:50%;background:radial-gradient(circle at 50% 40%,#4a4a4a,#111)}
.brand{display:flex;align-items:center;gap:4px;font-weight:800;font-size:9px;letter-spacing:.2px;color:var(--white);white-space:nowrap}
.brand-dot{display:inline-block;width:11px;height:11px;border-radius:50%;background:var(--red)}
.brand.on-light{color:var(--navy)}
.brand-lg{font-size:12px}
.brand-lg .brand-dot{width:16px;height:16px}
.side-brand{left:3px;top:50%;transform:translateY(-50%) rotate(-90deg);transform-origin:center;font-size:4.5px;font-weight:800;color:var(--red);white-space:nowrap;width:60px;text-align:center;margin-left:-24px}
.corner-dot{left:5px;top:5px;width:7px;height:7px;border-radius:50%;background:var(--red)}
.page-no{left:9px;bottom:5px;font-size:4px;color:var(--muted)}
.watermark{font-weight:800;color:var(--navy);opacity:.08;font-size:28px;white-space:nowrap}
.title{font-weight:700;color:var(--navy);font-size:15px}
.title::after{content:"";display:block;width:14px;height:3px;background:var(--red);margin-top:4px}
.title.center{text-align:center}
.title.center::after{margin-left:auto;margin-right:auto}
.title.on-dark{color:var(--white)}
.hero{font-weight:700;color:var(--white);line-height:1.05}
.body{font-size:4.6px;line-height:1.55;color:var(--ink)}
.body p+p{margin-top:5px}
.body.on-dark{color:#dfe6f2}
.lead{color:var(--red);font-weight:700}
.pill{border-radius:10px;font-weight:700;color:var(--white);background:var(--red);text-align:center}
.kicker{color:var(--red);font-size:7px}
.name{color:var(--navy);font-weight:700;font-size:13px}
.contact{font-size:4px;color:var(--red);display:flex;align-items:center;gap:5px}
.contact i{width:6px;height:6px;border-radius:50%;background:var(--navy);display:inline-block}
.card-label{font-weight:700;font-size:5px}
.small{font-size:4px;line-height:1.5}
table{border-collapse:collapse}
</style>
</head>
<body>
<main class="board">

<!-- Row 1 -->
<section class="slide">
  <div class="photo photo-city" role="img" aria-label="Blue-tinted city photograph"></div>
  <div class="brand" style="left:152px;top:36px"><i class="brand-dot"></i>Ledger Lanternfox</div>
  <div class="small" style="left:0;right:0;top:72px;text-align:center;color:#cdd8ea;letter-spacing:1px">www.ledgerlanternfox.example</div>
  <div class="hero" style="left:0;right:0;top:86px;text-align:center;font-size:24px">Presentation<br>Title Goes Here</div>
  <div style="left:0;right:0;top:140px;text-align:center;font-size:8px;color:#dfe6f2">Sub Title Goes Here</div>
  <div class="pill" style="left:148px;top:177px;width:90px;height:12px;font-size:5px;line-height:12px">Oct 2021</div>
</section>

<section class="slide">
  <div class="photo photo-city" style="bottom:36px" role="img" aria-label="Blue-tinted office photograph"></div>
  <div class="hero" style="left:18px;top:70px;font-size:19px">TITLE OF<br>PRESENTATION</div>
  <div class="small" style="left:18px;top:136px;color:#dfe6f2">Here Is A place for Credentials<br>Date: 2021 March</div>
  <div class="brand on-light" style="left:8px;top:192px"><i class="brand-dot"></i>Ledger Lanternfox</div>
  <div style="right:16px;top:200px;font-size:5px;font-weight:700;color:var(--red)">Presenter Name</div>
</section>

<section class="slide">
  <div class="photo photo-dark" role="img" aria-label="Blue-tinted server room photograph"></div>
  <div class="brand" style="left:24px;top:58px"><i class="brand-dot"></i>Ledger Lanternfox</div>
  <div class="hero" style="left:24px;top:84px;font-size:19px">TITLE OF<br>PRESENTATION</div>
  <div class="small" style="left:24px;top:152px;color:#dfe6f2">Here Is A place for Credentials<br>Date: 2021 March</div>
</section>

<!-- Row 2 -->
<section class="slide">
  <div class="photo photo-desk" role="img" aria-label="Photograph of a laptop on a desk with a person's hands"></div>
  <svg style="left:0;top:0" width="387" height="217"><polygon points="0,20 150,20 120,95 0,95" fill="#fff" opacity=".9"/><polygon points="110,112 387,112 387,167 88,167" fill="#e8262c"/></svg>
  <div class="brand on-light brand-lg" style="left:42px;top:48px"><i class="brand-dot"></i>Ledger Lanternfox</div>
  <div class="hero" style="left:150px;top:119px;font-size:19px;text-align:center">Presentation<br>Title Goes Here</div>
</section>

<section class="slide">
  <div class="watermark" style="right:18px;top:80px;font-size:34px">Ledger</div>
  <div class="brand on-light" style="left:24px;top:48px"><i class="brand-dot"></i>Ledger Lanternfox</div>
  <div style="left:24px;top:82px;font-size:24px;font-weight:700;color:var(--navy);line-height:1.02">Presentation<br>Title Goes Here</div>
  <div style="left:24px;top:135px;font-size:7px;color:var(--red)">Sub Title Goes Here</div>
  <div class="pill" style="left:22px;top:171px;width:118px;height:13px;font-size:5px;line-height:13px;letter-spacing:1px;font-weight:500">www.ledgerlanternfox.example</div>
</section>

<section class="slide">
  <div class="brand on-light" style="left:140px;top:22px"><i class="brand-dot"></i>Ledger Lanternfox</div>
</section>

<!-- Row 3 -->
<section class="slide fill-navy"><div class="brand" style="left:140px;top:22px"><i class="brand-dot"></i>Ledger Lanternfox</div></section>
<section class="slide fill-charcoal"><div class="brand" style="left:140px;top:22px"><i class="brand-dot"></i>Ledger Lanternfox</div></section>
<section class="slide fill-red"><div class="brand" style="left:140px;top:22px"><i class="brand-dot" style="background:#fff"></i>Ledger Lanternfox</div></section>

<!-- Row 4 -->
<section class="slide">
  <svg style="left:30px;top:30px" width="100" height="100"><g stroke="#1b3f7c" stroke-width="3"><line x1="5" y1="40" x2="40" y2="5"/><line x1="5" y1="50" x2="50" y2="5"/><line x1="5" y1="60" x2="60" y2="5"/><line x1="5" y1="70" x2="70" y2="5"/></g></svg>
  <div class="portrait" style="left:48px;top:38px;width:92px;height:92px" role="img" aria-label="Portrait photograph of the presenter"></div>
  <div style="left:48px;top:136px;display:grid;gap:8px">
    <div class="contact"><i></i>Here is a place for text</div>
    <div class="contact"><i></i>Here is a place for text</div>
    <div class="contact"><i></i>Here is a place for text</div>
  </div>
  <div style="left:165px;top:24px;width:1px;height:160px;background:var(--line)"></div>
  <div class="kicker" style="left:168px;top:14px">Manager</div>
  <div class="name" style="left:168px;top:24px;font-size:15px">Name, Last Name</div>
  <div class="body" style="left:168px;top:52px;width:200px"><p><span class="lead">Welcome to my deck, friends.</span> This area holds a short bio paragraph about who I am and what I do, written in plain clear words for any audience.</p><p>Here goes a second paragraph to describe focus areas, past work and things I care about, keeping each line short and easy to read.</p></div>
  <div class="brand on-light" style="left:183px;top:200px;font-size:5px"><i class="brand-dot" style="width:6px;height:6px"></i>Ledger Lanternfox</div>
  <div class="small" style="right:12px;bottom:5px;color:var(--muted)">10</div>
</section>

<section class="slide">
  <div class="title" style="left:22px;top:20px">Title And Body Slide</div>
  <div class="watermark" style="left:150px;top:90px;font-size:38px">Ledger</div>
  <div class="brand on-light" style="left:178px;top:200px;font-size:5px"><i class="brand-dot" style="width:6px;height:6px"></i>Ledger Lanternfox</div>
  <div class="small" style="right:12px;bottom:5px;color:var(--muted)">11</div>
</section>

<section class="slide">
  <div class="title" style="left:22px;top:18px">Title And Body Slide</div>
  <div class="body" style="left:22px;top:54px;width:350px"><p>This is sample body text that shows how a full paragraph looks on a content slide. Replace it with your own words and keep the main idea short, clear and easy to follow from the back of the room.</p><p>Here is a second block of sample text that fills the space. Use it to explain a point, share a fact or list key steps, then move on to the next idea without crowding the slide.</p><p>A third block of sample text sits here. Break long thoughts into smaller chunks, lead with the key word and let the audience read along at a calm pace while you speak.</p></div>
  <div class="brand on-light" style="left:178px;top:200px;font-size:5px"><i class="brand-dot" style="width:6px;height:6px"></i>Ledger Lanternfox</div>
</section>

<!-- Row 5 -->
<section class="slide">
  <i class="corner-dot"></i><div class="side-brand">Ledger Lanternfox</div>
  <div class="portrait" style="left:46px;top:52px;width:110px;height:110px;border-radius:10px" role="img" aria-label="Portrait photograph of the presenter"></div>
  <div class="pill" style="left:66px;top:150px;width:84px;height:14px;border-radius:7px;font-size:7px;line-height:14px">Your Name</div>
  <div class="title" style="left:194px;top:32px;font-size:16px">Welcome Message</div>
  <div style="left:190px;top:66px;font-size:22px;color:var(--line);font-weight:700">“</div>
  <div class="body" style="left:200px;top:64px;width:170px;text-align:center"><p>A short welcome note goes here to greet the room and set the tone for the talk ahead today.</p></div>
  <div class="body" style="left:200px;top:112px;width:170px;text-align:center"><p>Use this space to add a few lines about the goal of the session, what people will learn and how the time will be used, keeping it warm and direct.</p></div>
  <div class="page-no">12</div>
</section>

<section class="slide">
  <i class="corner-dot"></i><div class="side-brand">Ledger Lanternfox</div>
  <svg style="left:38px;top:30px" width="90" height="90"><g stroke="#1b3f7c" stroke-width="3"><line x1="5" y1="40" x2="40" y2="5"/><line x1="5" y1="50" x2="50" y2="5"/><line x1="5" y1="60" x2="60" y2="5"/></g></svg>
  <div class="portrait" style="left:52px;top:38px;width:84px;height:84px" role="img" aria-label="Portrait photograph of the presenter"></div>
  <div style="left:52px;top:148px;display:grid;gap:7px">
    <div class="contact"><i></i>Here is a place for text</div>
    <div class="contact"><i></i>Here is a place for text</div>
    <div class="contact"><i></i>Here is a place for text</div>
  </div>
  <div class="kicker" style="left:170px;top:30px">Manager</div>
  <div class="name" style="left:170px;top:40px;font-size:15px">Name, Last Name</div>
  <div class="body" style="left:170px;top:68px;width:200px"><p><span class="lead">Hello and welcome, everyone.</span> A short bio goes here to tell people who you are and why this topic matters to you.</p><p>Add a second paragraph with roles, skills and past projects, using short lines that are easy to read from afar.</p></div>
  <div class="page-no">14</div>
</section>

<section class="slide">
  <i class="corner-dot"></i><div class="side-brand">Ledger Lanternfox</div>
  <div class="fill-navy" style="right:28px;top:0;width:120px;height:160px"></div>
  <div style="left:235px;top:30px;width:122px;height:150px;background:#fff;box-shadow:0 2px 8px rgba(0,0,0,.12)"></div>
  <ol style="left:248px;top:46px;font-size:6.5px;color:var(--navy);list-style:none;display:grid;gap:11px">
    <li>1.&nbsp;&nbsp;Agenda item goes here</li><li>2.&nbsp;&nbsp;Agenda item goes here</li><li>3.&nbsp;&nbsp;Agenda item goes here</li><li>4.&nbsp;&nbsp;Agenda item goes here</li><li>5.&nbsp;&nbsp;Agenda item goes here</li><li>6.&nbsp;&nbsp;Agenda item goes here</li><li>7.&nbsp;&nbsp;Agenda item goes here</li>
  </ol>
  <div style="left:45px;top:72px;font-size:15px;font-weight:700;color:var(--navy);line-height:1.1">Here Goes<br>Title Of Your<br>Agenda</div>
  <div style="left:45px;top:126px;font-size:6px;color:var(--red)">Here Goes A Short Subtitle</div>
  <div class="page-no">15</div>
</section>

<!-- Row 6 -->
<section class="slide">
  <i class="corner-dot"></i><div class="side-brand">Ledger Lanternfox</div>
  <div class="title" style="left:34px;top:22px">Title And Body Slide</div>
  <div class="watermark" style="left:150px;top:88px;font-size:38px">Ledger</div>
  <div class="page-no">16</div>
</section>
<section class="slide">
  <i class="corner-dot"></i><div class="side-brand">Ledger Lanternfox</div>
  <div class="title" style="left:34px;top:22px">Title And Body Slide</div>
  <div class="page-no">17</div>
</section>
<section class="slide fill-navy">
  <i class="corner-dot"></i><div class="side-brand" style="color:#fff">Ledger Lanternfox</div>
  <div class="title on-dark" style="left:34px;top:22px">Title And Body Slide</div>
  <div class="page-no" style="color:#9fb0cc">18</div>
</section>

<!-- Row 7 -->
<section class="slide">
  <i class="corner-dot"></i><div class="side-brand">Ledger Lanternfox</div>
  <div class="title" style="left:34px;top:22px">Title And Body Slide</div>
  <div class="body" style="left:34px;top:62px;width:340px"><p>This is sample body text that shows how a full paragraph looks on a content slide. Replace it with your own words and keep the main idea short, clear and easy to follow from the back of the room.</p><p>Here is a second block of sample text that fills the space. Use it to explain a point, share a fact or list key steps, then move on to the next idea without crowding the slide.</p><p>A third block of sample text sits here. Break long thoughts into smaller chunks, lead with the key word and let the audience read along at a calm pace while you speak.</p></div>
  <div class="page-no">19</div>
</section>

<section class="slide">
  <div class="fill-navy" style="left:0;right:0;top:0;height:6px"></div>
  <div class="fill-red" style="left:0;right:0;bottom:0;height:10px"></div>
  <div style="left:14px;top:50px;font-size:52px;font-weight:700;color:#dde2ea">01</div>
  <div style="left:36px;top:54px;font-size:30px;font-weight:300;color:var(--charcoal);line-height:.95">Slide<br>Break</div>
  <div class="body" style="left:36px;top:130px;width:160px"><p>A short line of text about the next section goes here to guide the room into the new topic.</p></div>
  <div style="left:232px;top:64px;width:26px;height:26px;border-radius:50%;background:var(--red)"></div>
  <div style="left:232px;top:100px;font-size:13px;font-weight:800;color:var(--navy)">Ledger Lanternfox</div>
</section>

<section class="slide fill-navy">
  <div style="left:20px;top:44px;font-size:52px;font-weight:700;color:#3c5d96">01</div>
  <div style="left:44px;top:48px;font-size:30px;font-weight:300;color:#fff;line-height:.95">Slide<br>Break</div>
  <div class="body on-dark" style="left:44px;top:124px;width:170px"><p>A short line of text about the next section goes here to guide the room into the new topic.</p></div>
</section>

<!-- Row 8 -->
<section class="slide">
  <div class="photo photo-city" role="img" aria-label="Blue-tinted city photograph"></div>
  <div style="left:103px;top:18px;width:180px;height:180px;border-radius:50%;border:1px solid rgba(255,255,255,.7)"></div>
  <div style="left:0;right:0;top:38px;text-align:center;font-size:15px;font-weight:700;color:var(--red)">—— DEMO ——</div>
  <div class="body on-dark" style="left:118px;top:66px;width:150px;text-align:center;font-size:5.2px"><p>This demo area holds a short note about what people will see next, what to look for and how long the live part of the talk will take before questions open up again.</p></div>
</section>

<section class="slide fill-navy">
  <div style="left:102px;top:22px;width:182px;height:182px;border-radius:50%;background:#183a74"></div>
  <div style="left:104px;top:24px;width:178px;height:178px;border-radius:50%;border:1px solid rgba(255,255,255,.7)"></div>
  <div style="left:0;right:0;top:38px;text-align:center;font-size:15px;font-weight:700;color:#fff">—— DEMO ——</div>
  <div class="body on-dark" style="left:118px;top:66px;width:150px;text-align:center;font-size:5.2px"><p>This demo area holds a short note about what people will see next, what to look for and how long the live part of the talk will take before questions open up again.</p></div>
</section>

<section class="slide">
  <div class="photo photo-dark" role="img" aria-label="Blue-tinted technology photograph"></div>
  <div class="brand" style="left:22px;top:100px"><i class="brand-dot"></i>Ledger Lanternfox</div>
  <div style="left:148px;top:72px;width:2px;height:86px;background:var(--red)"></div>
  <div class="pill" style="left:166px;top:72px;width:64px;height:16px;font-size:10px;line-height:16px">DEMO</div>
  <div class="body on-dark" style="left:166px;top:100px;width:180px;font-size:6px"><p>This demo area holds a short note about what people will see next and what to look for during the live part of the talk.</p></div>
</section>

<!-- Row 9 -->
<section class="slide">
  <i class="corner-dot"></i><div class="side-brand">Ledger Lanternfox</div>
  <div class="fill-red" style="left:190px;top:28px;width:84px;height:80px"></div>
  <div class="photo-keyboard" style="left:212px;top:48px;width:150px;height:118px" role="img" aria-label="Photograph of a keyboard and monitor"></div>
  <div class="title" style="left:38px;top:60px;font-size:20px">Pic And Text</div>
  <div class="body" style="left:38px;top:102px;width:145px"><p>Sample text sits here beside the picture to explain what it shows and why it matters, using short lines that read well from a distance.</p></div>
  <div class="page-no">25</div>
</section>

<section class="slide">
  <div class="photo-mountain" style="left:0;top:0;width:168px;height:217px" role="img" aria-label="Photograph of a hiker standing on a mountain peak"></div>
  <div style="left:190px;top:66px;font-size:8px;font-weight:700;color:var(--navy);line-height:1.3;width:170px">Success is not only what you achieve in your life, but also what you inspire in the lives of others</div>
  <svg style="left:80px;top:150px" width="307" height="67"><polygon points="10,0 307,0 307,67 0,67" fill="#1b3f7c"/></svg>
  <div style="left:110px;top:158px;display:flex;gap:28px;color:#fff">
    <div style="width:60px"><div class="card-label">Sample heading</div><div class="small">Short note for this column of text.</div></div>
    <div style="width:60px"><div class="card-label">Sample heading</div><div class="small">Short note for this column of text.</div></div>
    <div style="width:60px"><div class="card-label">Sample heading</div><div class="small">Short note for this column of text.</div></div>
  </div>
</section>

<section class="slide">
  <i class="corner-dot"></i><div class="side-brand">Ledger Lanternfox</div>
  <div class="fill-navy" style="left:24px;right:0;top:0;height:100px"></div>
  <div style="left:24px;right:0;top:30px;text-align:center;font-size:15px;font-weight:700;color:#fff">Here Add Awesome Text</div>
  <div style="left:38px;right:10px;top:84px;display:flex;justify-content:space-around;text-align:center">
    <div style="width:90px"><svg width="34" height="34"><circle cx="17" cy="17" r="16" fill="#e8262c" stroke="#fff" stroke-width="2"/><circle cx="17" cy="17" r="6" fill="none" stroke="#fff" stroke-width="2"/></svg><div class="card-label" style="color:var(--navy);margin-top:4px">Project name</div><div class="small">Short note about this point goes here in two lines.</div></div>
    <div style="width:90px"><svg width="34" height="34"><circle cx="17" cy="17" r="16" fill="#e8262c" stroke="#fff" stroke-width="2"/><path d="M11 23 L23 11 M17 11 H23 V17" stroke="#fff" stroke-width="2" fill="none"/></svg><div class="card-label" style="color:var(--navy);margin-top:4px">Project name</div><div class="small">Short note about this point goes here in two lines.</div></div>
    <div style="width:90px"><svg width="34" height="34"><circle cx="17" cy="17" r="16" fill="#e8262c" stroke="#fff" stroke-width="2"/><path d="M11 18 L15 22 L23 12" stroke="#fff" stroke-width="2" fill="none"/></svg><div class="card-label" style="color:var(--navy);margin-top:4px">Project name</div><div class="small">Short note about this point goes here in two lines.</div></div>
  </div>
  <div class="page-no">27</div>
</section>

<!-- Row 10 -->
<section class="slide">
  <i class="corner-dot"></i><div class="side-brand">Ledger Lanternfox</div>
  <div class="title center" style="left:0;right:0;top:22px">3 Columns Slide</div>
  <div style="left:52px;top:90px;display:flex;gap:6px;color:#fff;text-align:center">
    <div style="width:88px;height:78px;background:var(--red);border-radius:4px;padding:14px 6px 0"><div class="card-label">Project name here</div><div class="small">Short sample text for this card goes here.</div></div>
    <div style="width:88px;height:78px;background:var(--navy);border-radius:4px;padding:14px 6px 0"><div class="card-label">Project name here</div><div class="small">Short sample text for this card goes here.</div></div>
    <div style="width:88px;height:78px;background:var(--gray);border-radius:4px;padding:14px 6px 0"><div class="card-label">Project name here</div><div class="small">Short sample text for this card goes here.</div></div>
  </div>
  <div style="left:84px;top:74px;display:flex;gap:70px">
    <i style="width:24px;height:24px;border-radius:50%;background:#fff;border:2px solid var(--red)"></i>
    <i style="width:24px;height:24px;border-radius:50%;background:#fff;border:2px solid var(--navy)"></i>
    <i style="width:24px;height:24px;border-radius:50%;background:#fff;border:2px solid var(--gray)"></i>
  </div>
  <div class="page-no">28</div>
</section>

<section class="slide">
  <i class="corner-dot"></i><div class="side-brand">Ledger Lanternfox</div>
  <div class="title center" style="left:0;right:0;top:18px">4 Column Slide</div>
  <div style="left:30px;top:78px;display:flex;gap:5px;color:#fff;text-align:center">
    <div style="width:80px;height:100px;background:var(--red);border-radius:4px;padding:18px 5px 0"><div class="card-label">Project name here</div><div class="small">Short sample text for this card goes here in a few lines.</div></div>
    <div style="width:80px;height:100px;background:var(--navy);border-radius:4px;padding:18px 5px 0"><div class="card-label">Project name here</div><div class="small">Short sample text for this card goes here in a few lines.</div></div>
    <div style="width:80px;height:100px;background:var(--navy-ink);border-radius:4px;padding:18px 5px 0"><div class="card-label">Project name here</div><div class="small">Short sample text for this card goes here in a few lines.</div></div>
    <div style="width:80px;height:100px;background:var(--gray);border-radius:4px;padding:18px 5px 0"><div class="card-label">Project name here</div><div class="small">Short sample text for this card goes here in a few lines.</div></div>
  </div>
  <div style="left:60px;top:62px;display:flex;gap:63px">
    <i style="width:22px;height:22px;border-radius:50%;background:#fff;border:2px solid var(--red)"></i><i style="width:22px;height:22px;border-radius:50%;background:#fff;border:2px solid var(--navy)"></i><i style="width:22px;height:22px;border-radius:50%;background:#fff;border:2px solid var(--navy-ink)"></i><i style="width:22px;height:22px;border-radius:50%;background:#fff;border:2px solid var(--gray)"></i>
  </div>
  <div class="page-no">29</div>
</section>

<section class="slide">
  <i class="corner-dot"></i><div class="side-brand">Ledger Lanternfox</div>
  <div class="title center" style="left:0;right:0;top:22px">5 Column Slide</div>
  <div style="left:54px;top:64px;display:flex;gap:6px;color:#fff;text-align:center">
    <div style="width:92px;height:52px;background:var(--navy);border-radius:3px;padding:8px 5px 0"><div class="card-label">Project name here</div><div class="small">Short sample text for this card.</div></div>
    <div style="width:92px;height:52px;background:var(--navy);border-radius:3px;padding:8px 5px 0"><div class="card-label">Project name here</div><div class="small">Short sample text for this card.</div></div>
    <div style="width:92px;height:52px;background:var(--navy);border-radius:3px;padding:8px 5px 0"><div class="card-label">Project name here</div><div class="small">Short sample text for this card.</div></div>
  </div>
  <div style="left:102px;top:128px;display:flex;gap:6px;color:#fff;text-align:center">
    <div style="width:92px;height:52px;background:var(--navy);border-radius:3px;padding:8px 5px 0"><div class="card-label">Project name here</div><div class="small">Short sample text for this card.</div></div>
    <div style="width:92px;height:52px;background:var(--navy);border-radius:3px;padding:8px 5px 0"><div class="card-label">Project name here</div><div class="small">Short sample text for this card.</div></div>
  </div>
  <div class="page-no">30</div>
</section>

<!-- Row 11 -->
<section class="slide">
  <svg style="left:0;top:0" width="387" height="217"><polygon points="22,0 165,0 300,217 22,217" fill="#1b3f7c"/></svg>
  <div class="side-brand">Ledger Lanternfox</div>
  <div style="left:176px;top:48px;width:210px;height:122px;background:#2b2b2d;border-radius:5px"></div>
  <div style="left:182px;top:53px;width:198px;height:110px;background:#707375;text-align:center;color:#fff;font-size:6px;line-height:110px">HERE YOU CAN ADD A SCREENSHOT</div>
  <div style="left:163px;top:170px;width:224px;height:5px;background:#c9ccd1;border-radius:0 0 4px 4px"></div>
  <div class="title on-dark" style="left:44px;top:70px;font-size:15px;line-height:1.15">A Place for<br>Screenshot</div>
  <div class="body on-dark" style="left:44px;top:122px;width:112px"><p>Short sample text about the screenshot goes here, kept to a few clear lines.</p></div>
  <div class="page-no" style="color:#9fb0cc">31</div>
</section>

<section class="slide">
  <i class="corner-dot"></i><div class="side-brand">Ledger Lanternfox</div>
  <div class="title center" style="left:0;right:0;top:18px">6 Columns Slide</div>
  <div style="left:40px;top:62px;display:grid;grid-template-columns:168px 168px;row-gap:12px">
    <div style="display:flex;gap:10px"><i style="width:14px;height:14px;border:1.5px solid var(--navy);border-radius:2px"></i><div><div class="card-label" style="color:var(--navy)">Project name</div><div class="small" style="width:120px">Short sample text for this column goes here in two lines.</div></div></div>
    <div style="display:flex;gap:10px"><i style="width:14px;height:14px;border:1.5px solid var(--navy);border-radius:2px"></i><div><div class="card-label" style="color:var(--navy)">Project name</div><div class="small" style="width:120px">Short sample text for this column goes here in two lines.</div></div></div>
    <div style="display:flex;gap:10px"><i style="width:14px;height:14px;border:1.5px solid var(--navy);border-radius:50%"></i><div><div class="card-label" style="color:var(--navy)">Project name</div><div class="small" style="width:120px">Short sample text for this column goes here in two lines.</div></div></div>
    <div style="display:flex;gap:10px"><i style="width:14px;height:14px;border:1.5px solid var(--navy);border-radius:50%"></i><div><div class="card-label" style="color:var(--navy)">Project name</div><div class="small" style="width:120px">Short sample text for this column goes here in two lines.</div></div></div>
    <div style="display:flex;gap:10px"><i style="width:14px;height:14px;border:1.5px solid var(--navy);border-radius:2px"></i><div><div class="card-label" style="color:var(--navy)">Project name</div><div class="small" style="width:120px">Short sample text for this column goes here in two lines.</div></div></div>
    <div style="display:flex;gap:10px"><i style="width:14px;height:14px;border:1.5px solid var(--navy);border-radius:2px"></i><div><div class="card-label" style="color:var(--navy)">Project name</div><div class="small" style="width:120px">Short sample text for this column goes here in two lines.</div></div></div>
  </div>
  <div class="page-no">32</div>
</section>

<section class="slide">
  <i class="corner-dot"></i><div class="side-brand">Ledger Lanternfox</div>
  <div class="title center" style="left:0;right:0;top:18px">Table Slide</div>
  <table style="left:40px;top:56px;width:330px;font-size:4.5px;text-align:center">
    <tr style="color:#fff"><td style="width:82px"></td><td style="background:var(--red);height:10px">Your Text Here</td><td style="background:var(--red)">Your Text Here</td><td style="background:var(--red)">Your Text Here</td><td style="background:var(--red)">Your Text Here</td></tr>
    <tr style="height:16px"><td style="background:var(--navy);color:#fff;font-weight:700">You can replace this text</td><td>data</td><td>data</td><td>data</td><td>data</td></tr>
    <tr style="height:16px;background:#f3f5f8"><td style="background:var(--navy);color:#fff;font-weight:700">You can replace this text</td><td>data</td><td style="color:var(--navy);font-size:8px">✕</td><td>data</td><td>data</td></tr>
    <tr style="height:16px"><td style="background:var(--navy);color:#fff;font-weight:700">You can replace this text</td><td>data</td><td style="color:var(--navy);font-size:8px">✓</td><td>data</td><td>data</td></tr>
    <tr style="height:16px;background:#f3f5f8"><td style="background:var(--navy);color:#fff;font-weight:700">You can replace this text</td><td>data</td><td style="color:var(--navy);font-size:8px">✕</td><td>data</td><td>data</td></tr>
    <tr style="height:16px"><td style="background:var(--navy);color:#fff;font-weight:700">You can replace this text</td><td>data</td><td style="color:var(--navy);font-size:8px">✓</td><td>data</td><td>data</td></tr>
    <tr style="height:16px;background:#f3f5f8"><td style="background:var(--navy);color:#fff;font-weight:700">You can replace this text</td><td>data</td><td style="color:var(--navy);font-size:8px">✓</td><td>data</td><td>data</td></tr>
    <tr style="height:16px"><td style="background:var(--navy);color:#fff;font-weight:700">You can replace this text</td><td>data</td><td style="color:var(--navy);font-size:8px">✕</td><td>data</td><td>data</td></tr>
  </table>
  <div class="page-no">33</div>
</section>

<!-- Row 12 -->
<section class="slide">
  <div class="fill-navy" style="left:22px;top:0;width:200px;height:217px"></div>
  <div class="side-brand">Ledger Lanternfox</div>
  <div class="title on-dark" style="left:40px;top:96px;font-size:16px">Table Slide</div>
  <div style="left:162px;top:34px;width:212px;height:158px;background:#fff;border-radius:6px;box-shadow:0 2px 8px rgba(0,0,0,.15)"></div>
  <table style="left:170px;top:42px;width:196px;font-size:4.6px;text-align:center">
    <tr style="background:var(--navy);color:#fff;font-weight:700;height:12px"><td>Text</td><td>Text</td><td>Text</td><td>Text</td><td>Text</td></tr>
    <tr style="height:20px;border-bottom:1px solid var(--line)"><td style="font-weight:700;color:var(--navy)">Data</td><td>Data</td><td>Data</td><td>Data</td><td>Data</td></tr>
    <tr style="height:20px;border-bottom:1px solid var(--line)"><td style="font-weight:700;color:var(--navy)">Data</td><td>Data</td><td>Data</td><td>Data</td><td>Data</td></tr>
    <tr style="height:20px;border-bottom:1px solid var(--line)"><td style="font-weight:700;color:var(--navy)">Data</td><td>Data</td><td>Data</td><td>Data</td><td>Data</td></tr>
    <tr style="height:20px;border-bottom:1px solid var(--line)"><td style="font-weight:700;color:var(--navy)">Data</td><td>Data</td><td>Data</td><td>Data</td><td>Data</td></tr>
    <tr style="height:20px;border-bottom:1px solid var(--line)"><td style="font-weight:700;color:var(--navy)">Data</td><td>Data</td><td>Data</td><td>Data</td><td>Data</td></tr>
    <tr style="height:20px"><td style="font-weight:700;color:var(--navy)">Data</td><td>Data</td><td>Data</td><td>Data</td><td>Data</td></tr>
  </table>
  <div class="page-no" style="color:#9fb0cc">34</div>
</section>

<section class="slide">
  <i class="corner-dot"></i><div class="side-brand">Ledger Lanternfox</div>
  <div class="title center" style="left:0;right:0;top:16px">Table Slide</div>
  <table style="left:40px;top:52px;width:324px;font-size:5px;text-align:center">
    <tr style="background:var(--navy);color:#fff;font-weight:700;height:12px"><td>Text</td><td>Text</td><td>Text</td><td>Text</td><td>Text</td></tr>
    <tr style="height:18px;border-bottom:1px solid var(--line)"><td style="font-weight:700;color:var(--navy)">Data</td><td>Data</td><td>Data</td><td>Data</td><td>Data</td></tr>
    <tr style="height:18px;border-bottom:1px solid var(--line);background:#f3f5f8"><td style="font-weight:700;color:var(--navy)">Data</td><td>Data</td><td>Data</td><td>Data</td><td>Data</td></tr>
    <tr style="height:18px;border-bottom:1px solid var(--line)"><td style="font-weight:700;color:var(--navy)">Data</td><td>Data</td><td>Data</td><td>Data</td><td>Data</td></tr>
    <tr style="height:18px;border-bottom:1px solid var(--line);background:#f3f5f8"><td style="font-weight:700;color:var(--navy)">Data</td><td>Data</td><td>Data</td><td>Data</td><td>Data</td></tr>
    <tr style="height:18px;border-bottom:1px solid var(--line)"><td style="font-weight:700;color:var(--navy)">Data</td><td>Data</td><td>Data</td><td>Data</td><td>Data</td></tr>
    <tr style="height:18px;background:#f3f5f8"><td style="font-weight:700;color:var(--navy)">Data</td><td>Data</td><td>Data</td><td>Data</td><td>Data</td></tr>
  </table>
  <div class="page-no">35</div>
</section>

<section class="slide">
  <i class="corner-dot"></i><div class="side-brand">Ledger Lanternfox</div>
  <div class="title" style="left:34px;top:20px">Smart Art Slide</div>
  <div style="left:34px;top:64px;display:grid;gap:14px">
    <div style="display:flex;gap:8px"><i style="width:12px;height:12px;border:1.5px solid var(--navy);border-radius:50%"></i><div><div class="card-label" style="color:var(--navy)">Sample point</div><div class="small" style="width:120px">Short sample text for this point goes here in two lines.</div></div></div>
    <div style="display:flex;gap:8px"><i style="width:12px;height:12px;border:1.5px solid var(--navy);border-radius:50%"></i><div><div class="card-label" style="color:var(--navy)">Sample point</div><div class="small" style="width:120px">Short sample text for this point goes here in two lines.</div></div></div>
    <div style="display:flex;gap:8px"><i style="width:12px;height:12px;border:1.5px solid var(--navy);border-radius:50%"></i><div><div class="card-label" style="color:var(--navy)">Sample point</div><div class="small" style="width:120px">Short sample text for this point goes here in two lines.</div></div></div>
  </div>
  <svg style="left:200px;top:50px" width="180" height="160"><polygon points="90,5 126,72 54,72" fill="#1b3f7c"/><polygon points="50,78 88,78 88,150 10,150" fill="#e8262c"/><polygon points="92,78 130,78 170,150 92,150" fill="#7c7c7e"/></svg>
  <div style="left:270px;top:90px;width:40px;text-align:center;color:#fff;font-size:4.5px;font-weight:700">Project name</div>
  <div style="left:222px;top:150px;width:60px;text-align:center;color:#fff;font-size:4.5px;font-weight:700">Project name</div>
  <div style="left:300px;top:150px;width:60px;text-align:center;color:#fff;font-size:4.5px;font-weight:700">Project name</div>
  <div class="page-no">36</div>
</section>

<!-- Row 13 -->
<section class="slide">
  <i class="corner-dot"></i><div class="side-brand">Ledger Lanternfox</div>
  <div class="title center" style="left:0;right:0;top:18px">Here is Quotes</div>
  <div style="left:38px;top:58px;font-size:22px;font-weight:800;color:var(--red)">”</div>
  <div style="left:216px;top:58px;font-size:22px;font-weight:800;color:var(--navy)">”</div>
  <div class="body" style="left:38px;top:90px;width:150px;font-size:5.4px"><p>A short quote goes here in a few lines so the room can read it with ease from afar.</p></div>
  <div class="body" style="left:216px;top:90px;width:150px;font-size:5.4px"><p>A short quote goes here in a few lines so the room can read it with ease from afar.</p></div>
  <div style="left:40px;top:170px;display:flex;gap:6px;align-items:center"><i style="width:14px;height:14px;border-radius:50%;background:var(--line)"></i><div class="small"><b style="color:var(--navy)">Your Name</b><br>Founder</div></div>
  <div style="left:218px;top:170px;display:flex;gap:6px;align-items:center"><i style="width:14px;height:14px;border-radius:50%;background:var(--line)"></i><div class="small"><b style="color:var(--navy)">Your Name</b><br>Founder</div></div>
  <div class="page-no">37</div>
</section>

<section class="slide">
  <i class="corner-dot"></i><div class="side-brand">Ledger Lanternfox</div>
  <div class="title center" style="left:0;right:0;top:18px">Here Is Statistics</div>
  <svg style="left:28px;top:52px" width="160" height="160"><circle cx="60" cy="80" r="58" fill="#1b3f7c"/><circle cx="60" cy="100" r="38" fill="#e8262c"/><circle cx="60" cy="120" r="18" fill="#7c7c7e"/><g fill="#fff" font-family="Raleway,sans-serif" font-weight="700" font-size="12" text-anchor="middle"><text x="60" y="52">$</text><text x="60" y="88">$</text><text x="60" y="125">$</text></g><g stroke="#ccc" stroke-width="1"><line x1="90" y1="48" x2="120" y2="48"/><line x1="98" y1="84" x2="120" y2="84"/><line x1="78" y1="120" x2="120" y2="120"/></g></svg>
  <div style="left:150px;top:92px;font-size:9px;font-weight:700;color:var(--navy);display:grid;gap:26px"><span>5M</span><span>2M</span><span>1M</span></div>
  <div style="left:230px;top:86px;display:grid;gap:12px">
    <div style="display:flex;gap:6px"><i style="width:10px;height:10px;background:var(--navy)"></i><div><div class="card-label" style="color:var(--navy)">Sample heading</div><div class="small" style="width:110px">Short sample text for this item.</div></div></div>
    <div style="display:flex;gap:6px"><i style="width:10px;height:10px;background:var(--red)"></i><div><div class="card-label" style="color:var(--navy)">Sample heading</div><div class="small" style="width:110px">Short sample text for this item.</div></div></div>
    <div style="display:flex;gap:6px"><i style="width:10px;height:10px;background:var(--gray)"></i><div><div class="card-label" style="color:var(--navy)">Sample heading</div><div class="small" style="width:110px">Short sample text for this item.</div></div></div>
  </div>
  <div class="page-no">38</div>
</section>

<section class="slide">
  <i class="corner-dot"></i><div class="side-brand">Ledger Lanternfox</div>
  <div class="title center" style="left:0;right:0;top:18px">Here Add Your Title</div>
  <div class="body" style="left:70px;top:56px;width:260px;text-align:center;font-size:4.4px"><p>A short intro line about these numbers goes here to explain what each ring shows and why the values matter for the work.</p></div>
  <svg style="left:80px;top:96px" width="240" height="60" font-family="Raleway,sans-serif">
    <circle cx="30" cy="30" r="24" fill="none" stroke="#eee" stroke-width="4"/><circle cx="30" cy="30" r="24" fill="none" stroke="#e8262c" stroke-width="4" stroke-dasharray="75 151" transform="rotate(-90 30 30)"/><text x="30" y="34" text-anchor="middle" font-size="11" font-weight="700" fill="#1b3f7c">50%</text>
    <circle cx="120" cy="30" r="24" fill="none" stroke="#eee" stroke-width="4"/><circle cx="120" cy="30" r="24" fill="none" stroke="#e8262c" stroke-width="4" stroke-dasharray="113 151" transform="rotate(-90 120 30)"/><text x="120" y="34" text-anchor="middle" font-size="11" font-weight="700" fill="#1b3f7c">75%</text>
    <circle cx="210" cy="30" r="24" fill="none" stroke="#eee" stroke-width="4"/><circle cx="210" cy="30" r="24" fill="none" stroke="#e8262c" stroke-width="4" stroke-dasharray="60 151" transform="rotate(-90 210 30)"/><text x="210" y="34" text-anchor="middle" font-size="11" font-weight="700" fill="#1b3f7c">40%</text>
  </svg>
  <div style="left:80px;top:164px;width:240px;display:flex;justify-content:space-between;text-align:center" class="small"><span style="width:60px">Short note for this value.</span><span style="width:60px">Short note for this value.</span><span style="width:60px">Short note for this value.</span></div>
</section>

<!-- Row 14 -->
<section class="slide">
  <i class="corner-dot"></i><div class="side-brand">Ledger Lanternfox</div>
  <div class="title center" style="left:0;right:0;top:16px">Here is Statistics</div>
  <div style="left:30px;top:66px;width:104px;height:112px;background:#fff;box-shadow:0 1px 6px rgba(0,0,0,.12)"></div>
  <div style="left:30px;top:66px;width:104px;height:50px;background:var(--navy);color:#fff;text-align:center;padding-top:10px"><div style="font-size:15px">$0.5M</div><div class="small">Revenue</div></div>
  <div style="left:30px;top:126px;width:104px;text-align:center;color:var(--red)"><div style="font-size:14px">-0.28%</div><div class="small">Revenue</div></div>
  <svg style="left:150px;top:62px" width="230" height="130" font-family="Raleway,sans-serif" font-size="4" fill="#888">
    <g stroke="#eee"><line x1="30" y1="8" x2="225" y2="8"/><line x1="30" y1="28" x2="225" y2="28"/><line x1="30" y1="48" x2="225" y2="48"/><line x1="30" y1="68" x2="225" y2="68"/><line x1="30" y1="88" x2="225" y2="88"/><line x1="30" y1="108" x2="225" y2="108"/></g>
    <text x="2" y="10">$800,000</text><text x="2" y="30">$600,000</text><text x="2" y="50">$400,000</text><text x="2" y="70">$200,000</text><text x="2" y="90">$100,000</text><text x="2" y="110">$0</text>
    <polyline points="32,100 50,98 68,92 86,96 104,84 122,88 140,62 158,70 176,40 194,54 212,18 222,30" fill="none" stroke="#e8262c" stroke-width="1.6"/>
    <g text-anchor="middle"><text x="32" y="120">Jan</text><text x="50" y="120">Feb</text><text x="68" y="120">Mar</text><text x="86" y="120">Apr</text><text x="104" y="120">May</text><text x="122" y="120">Jun</text><text x="140" y="120">Jul</text><text x="158" y="120">Aug</text><text x="176" y="120">Sep</text><text x="194" y="120">Oct</text><text x="212" y="120">Nov</text><text x="222" y="126">Dec</text></g>
  </svg>
  <div class="page-no">40</div>
</section>

<section class="slide">
  <i class="corner-dot"></i><div class="side-brand">Ledger Lanternfox</div>
  <div class="title center" style="left:0;right:0;top:18px">Company Timeline</div>
  <svg style="left:34px;top:70px" width="340" height="34" font-family="Raleway,sans-serif" font-size="6.5" font-weight="700" fill="#fff">
    <polygon points="0,2 58,2 66,16 58,30 0,30 8,16" fill="#e8262c"/><text x="33" y="19" text-anchor="middle">STEP 01</text>
    <polygon points="64,2 122,2 130,16 122,30 64,30 72,16" fill="#1b3f7c"/><text x="97" y="19" text-anchor="middle">STEP 02</text>
    <polygon points="128,2 186,2 194,16 186,30 128,30 136,16" fill="#e8262c"/><text x="161" y="19" text-anchor="middle">STEP 03</text>
    <polygon points="192,2 250,2 258,16 250,30 192,30 200,16" fill="#1b3f7c"/><text x="225" y="19" text-anchor="middle">STEP 04</text>
    <polygon points="256,2 314,2 322,16 314,30 256,30 264,16" fill="#e8262c"/><text x="289" y="19" text-anchor="middle">STEP 05</text>
  </svg>
  <div style="left:38px;top:124px;display:flex;gap:8px;text-align:center">
    <div style="width:56px"><div class="card-label" style="color:var(--navy)">Project name</div><div class="small">Short sample text for this step.</div></div>
    <div style="width:56px"><div class="card-label" style="color:var(--navy)">Project name</div><div class="small">Short sample text for this step.</div></div>
    <div style="width:56px"><div class="card-label" style="color:var(--navy)">Project name</div><div class="small">Short sample text for this step.</div></div>
    <div style="width:56px"><div class="card-label" style="color:var(--navy)">Project name</div><div class="small">Short sample text for this step.</div></div>
    <div style="width:56px"><div class="card-label" style="color:var(--navy)">Project name</div><div class="small">Short sample text for this step.</div></div>
  </div>
  <div class="page-no">41</div>
</section>

<section class="slide">
  <i class="corner-dot"></i><div class="side-brand">Ledger Lanternfox</div>
  <div class="title center" style="left:0;right:0;top:18px">Q&amp;A Slide</div>
  <div style="left:52px;top:56px;display:grid;grid-template-columns:150px 150px;column-gap:24px;row-gap:12px">
    <div style="display:flex;gap:8px"><b style="width:18px;height:18px;background:var(--navy);color:#fff;text-align:center;line-height:18px;font-size:9px">Q</b><span class="small" style="width:110px">Sample question text goes here in a short line or two.</span></div>
    <div style="display:flex;gap:8px"><b style="width:18px;height:18px;background:var(--red);color:#fff;text-align:center;line-height:18px;font-size:9px">A</b><span class="small" style="width:110px">Sample answer text goes here in a short line or two.</span></div>
    <div style="display:flex;gap:8px"><b style="width:18px;height:18px;background:var(--navy);color:#fff;text-align:center;line-height:18px;font-size:9px">Q</b><span class="small" style="width:110px">Sample question text goes here in a short line or two.</span></div>
    <div style="display:flex;gap:8px"><b style="width:18px;height:18px;background:var(--red);color:#fff;text-align:center;line-height:18px;font-size:9px">A</b><span class="small" style="width:110px">Sample answer text goes here in a short line or two.</span></div>
    <div style="display:flex;gap:8px"><b style="width:18px;height:18px;background:var(--navy);color:#fff;text-align:center;line-height:18px;font-size:9px">Q</b><span class="small" style="width:110px">Sample question text goes here in a short line or two.</span></div>
    <div style="display:flex;gap:8px"><b style="width:18px;height:18px;background:var(--red);color:#fff;text-align:center;line-height:18px;font-size:9px">A</b><span class="small" style="width:110px">Sample answer text goes here in a short line or two.</span></div>
    <div style="display:flex;gap:8px"><b style="width:18px;height:18px;background:var(--navy);color:#fff;text-align:center;line-height:18px;font-size:9px">Q</b><span class="small" style="width:110px">Sample question text goes here in a short line or two.</span></div>
    <div style="display:flex;gap:8px"><b style="width:18px;height:18px;background:var(--red);color:#fff;text-align:center;line-height:18px;font-size:9px">A</b><span class="small" style="width:110px">Sample answer text goes here in a short line or two.</span></div>
  </div>
  <div class="page-no">42</div>
</section>

<!-- Row 15 -->
<section class="slide">
  <i class="corner-dot"></i><div class="side-brand">Ledger Lanternfox</div>
  <div class="brand on-light" style="left:54px;top:56px"><i class="brand-dot"></i>Ledger Lanternfox</div>
  <div style="left:46px;top:82px;width:104px;height:100px;background:#fff;box-shadow:0 1px 6px rgba(0,0,0,.12)"></div>
  <div style="left:46px;top:82px;width:104px;height:26px;background:var(--navy);display:flex;align-items:center;gap:8px;padding-left:8px;color:#fff;font-size:4.2px"><i style="width:8px;height:8px;border-radius:50%;border:1px solid #fff"></i>www.ledgerlanternfox.example</div>
  <div style="left:54px;top:118px;display:flex;align-items:center;gap:8px;font-size:4px;color:var(--ink)"><i style="width:8px;height:8px;border-radius:50%;background:var(--navy)"></i>Here is a place<br>for your text</div>
  <div style="left:54px;top:152px;display:flex;align-items:center;gap:8px;font-size:4px;color:var(--ink)"><i style="width:8px;height:6px;border:1px solid var(--navy)"></i>hello@ledgerlanternfox.example</div>
  <div style="left:210px;top:94px;font-size:22px;font-weight:700;color:var(--navy)">THANK YOU</div>
</section>

<section class="slide">
  <i class="corner-dot"></i><div class="side-brand">Ledger Lanternfox</div>
  <svg style="left:80px;top:28px" width="240" height="170">
    <polyline points="10,40 10,12 200,4 206,30" fill="none" stroke="#1b3f7c" stroke-width="2"/>
    <polyline points="18,34 18,20 196,14" fill="none" stroke="#e8262c" stroke-width="2"/>
    <polygon points="22,40 214,30 222,140 16,150" fill="#fff" stroke="#eceef2" stroke-width="1"/>
    <polyline points="40,150 110,166 230,140 226,110" fill="none" stroke="#1b3f7c" stroke-width="2"/>
    <polyline points="60,156 120,160 216,148" fill="none" stroke="#e8262c" stroke-width="2"/>
  </svg>
  <div style="left:0;right:0;top:100px;text-align:center;font-size:20px;font-weight:700;color:var(--navy)">Questions?</div>
  <div class="page-no">44</div>
</section>

</main>
</body>
</html>
```